Tech business card design

We need an amazing business card design for our new business 'Pexla' a marketing tech startup based in Sydney, Australia. We provide an online marketplace for businesses to search and buy advertising media, connect with service providers and learn more about marketing. We wish to communicate 'cool tech', reliability and professionalism and design based around our logo.

Target Market(s)

Business Owners

Contact Information for Business Card

Name
Position
Email Address
Website
Phone Number

Font styles to use
Other font styles liked:
• Avenir & Avenir Next

Colors

Designer to choose colors to be used in the design.

```html
<!DOCTYPE html>
<html lang="en">
<head>
<meta charset="utf-8">
<title>Pexla Business Card</title>
<link href="https://fonts.googleapis.com/css2?family=Open+Sans:wght@400;700;800&display=swap" rel="stylesheet">
<style>
  :root {
    --backdrop: #e1dede;
    --paper: #ffffff;
    --navy: #121439;
    --ink: #1b2048;
    --card-edge: #5a5a5a;
    --muted-light: #c8c9d8;
  }
  * { margin: 0; padding: 0; box-sizing: border-box; }
  html, body {
    width: 975px; height: 1200px; overflow: hidden;
    background: var(--backdrop);
    font-family: "Open Sans", Arial, sans-serif;
  }
  .canvas { position: relative; width: 975px; height: 1200px; }
  .card {
    position: absolute; width: 864px; height: 496px; border-radius: 37px;
  }
  .card--front {
    left: 56px; top: 83px; background: var(--paper);
    border: 1px solid var(--card-edge); color: var(--ink);
  }
  .card--back { left: 52px; top: 631px; background: var(--navy); }

  .wordmark {
    position: absolute; font-weight: 800; line-height: 1; letter-spacing: -2px;
  }
  .card--front .wordmark {
    left: 79px; top: 46px; font-size: 118px; color: var(--navy);
  }
  .card--back .wordmark {
    left: 0; right: 0; top: 170px; text-align: center;
    font-size: 140px; color: #ffffff;
  }
  .divider {
    position: absolute; left: 80px; top: 287px; width: 398px; height: 3px;
    background: var(--ink);
  }
  .contacts { position: absolute; left: 80px; top: 316px; list-style: none; }
  .contacts li {
    display: flex; align-items: center; gap: 9px;
    font-size: 21px; height: 33px;
  }
  .contacts svg { width: 22px; height: 22px; flex: none; }
  .identity { position: absolute; left: 505px; top: 255px; }
  .identity__name { font-size: 26px; font-weight: 700; line-height: 34px; letter-spacing: 0.3px; }
  .identity__role { font-size: 25px; line-height: 34px; }
  .identity__address { margin-top: 29px; font-size: 21px; line-height: 29px; }
  .back-url {
    position: absolute; left: 0; right: 0; top: 400px; text-align: center;
    font-size: 25px; letter-spacing: 4px; color: var(--muted-light);
  }
</style>
</head>
<body>
<div class="canvas">
  <section class="card card--front">
    <div class="wordmark">pexla</div>
    <div class="divider"></div>
    <ul class="contacts">
      <li>
        <svg viewBox="0 0 24 24" aria-hidden="true"><circle cx="12" cy="12" r="10.5" fill="none" stroke="currentColor" stroke-width="2"/><path d="M8.3 6.8l1.8-.4 1.2 2.8-1.3 1a7 7 0 0 0 3.8 3.8l1-1.3 2.8 1.2-.4 1.8c-4.8.6-9.5-4.1-8.9-8.9z" fill="currentColor"/></svg>
        014-726-3958
      </li>
      <li>
        <svg viewBox="0 0 24 24" aria-hidden="true"><rect x="1.5" y="5" width="21" height="14" fill="currentColor"/><path d="M2 5.5l10 7.5 10-7.5M2 18.5l7.5-7M22 18.5l-7.5-7" fill="none" stroke="#fff" stroke-width="1.6"/></svg>
        info@pexla.com
      </li>
      <li>
        <svg viewBox="0 0 24 24" aria-hidden="true" fill="none" stroke="currentColor" stroke-width="1.6"><circle cx="12" cy="12" r="10"/><ellipse cx="12" cy="12" rx="4.5" ry="10"/><path d="M2 12h20M3.5 7h17M3.5 17h17M12 2v20"/></svg>
        www.pexla.com
      </li>
    </ul>
    <div class="identity">
      <p class="identity__name">MARA ELLSTON</p>
      <p class="identity__role">Position</p>
      <p class="identity__address">Street name City Name,<br>Zipcode,012345</p>
    </div>
  </section>

  <section class="card card--back">
    <div class="wordmark">pexla</div>
    <p class="back-url">www.pexla.com</p>
  </section>
</div>
</body>
</html>
```